BOLD & MINIMALIST DESIGN NEEDED

We want a very bold but minimalistic business card design that is impactful and utilizes both sides of the business card. Our current logo is included for your use.

We want bold fonts and good use of negative space. We don't want the logo to overpower the design.

Target Market(s)

Professionals who are building new commercial buildings.

Industry/Entity Type

Construction

Contact Information for Business Card

Name, Title, email, office phone, cell phone, website

Font styles to use
Serif
Sans Serif

Requirements
Must have
• Bold design!

```html
<!DOCTYPE html>
<html lang="en">
<head>
<meta charset="utf-8">
<title>Ridgeline Design + Build — Business Card</title>
<link href="https://fonts.googleapis.com/css2?family=Montserrat:wght@400;500;800;900&display=swap" rel="stylesheet">
<style>
  :root {
    --backdrop: #2b2b2b;
    --brand-green: #86c440;
    --card-black: #121212;
    --ink-white: #ffffff;
    --ink-soft: #e9e9e9;
  }
  * { box-sizing: border-box; margin: 0; padding: 0; }
  html, body {
    width: 1200px; height: 689px; overflow: hidden;
    background: var(--backdrop);
    font-family: "Montserrat", Arial, sans-serif;
  }
  .canvas {
    position: relative; width: 1200px; height: 689px;
    display: flex; align-items: center; justify-content: center; gap: 48px;
  }
  .card {
    position: relative; width: 540px; height: 309px;
    border-radius: 24px; overflow: hidden;
    box-shadow: 0 18px 40px rgba(0,0,0,.45);
  }
  .card--front { background: var(--brand-green); }
  .card--back { background: var(--card-black); color: var(--ink-white); }

  /* Wordmark */
  .wordmark {
    position: absolute; display: flex; flex-direction: column; align-items: center;
    color: var(--ink-white); font-weight: 900; text-transform: uppercase;
  }
  .wordmark__name { line-height: 1; letter-spacing: .01em; }
  .wordmark__tag { letter-spacing: .38em; border-top: 1.5px solid var(--ink-white); line-height: 1; }

  .card--front .wordmark { left: 0; right: 0; top: 108px; }
  .card--front .wordmark__name { font-size: 66px; }
  .card--front .wordmark__tag { font-size: 19px; margin-top: 8px; padding-top: 8px; width: 380px; text-align: center; }

  .card--back .wordmark { left: 150px; top: 218px; }
  .card--back .wordmark__name { font-size: 40px; }
  .card--back .wordmark__tag { font-size: 12px; margin-top: 5px; padding-top: 5px; width: 232px; text-align: center; }

  /* Back details */
  .address {
    position: absolute; right: 34px; top: 30px; text-align: right;
    font-size: 13px; font-weight: 500; line-height: 1.5; color: var(--ink-soft);
  }
  .person { position: absolute; left: 34px; top: 116px; }
  .person__name { font-size: 26px; font-weight: 800; color: var(--brand-green); letter-spacing: .02em; text-transform: uppercase; }
  .person__title { font-size: 13px; font-weight: 500; letter-spacing: .06em; margin-top: 2px; text-transform: uppercase; }

  .contacts {
    position: absolute; right: 34px; top: 112px; list-style: none;
    font-size: 13px; font-weight: 500; line-height: 1.55; text-align: right;
  }
  .contacts li { display: flex; align-items: center; justify-content: flex-end; gap: 7px; }
  .contacts svg { width: 12px; height: 12px; fill: var(--brand-green); flex: none; }
</style>
</head>
<body>
<main class="canvas">

  <section class="card card--front" aria-label="Card front">
    <div class="wordmark">
      <span class="wordmark__name">Ridgeline</span>
      <span class="wordmark__tag">Design + Build</span>
    </div>
  </section>

  <section class="card card--back" aria-label="Card back">
    <p class="address">Your address<br>City State, Zip 1234</p>

    <div class="person">
      <h1 class="person__name">Ravi Mehta</h1>
      <p class="person__title">Owner-CEO</p>
    </div>

    <ul class="contacts">
      <li>123 456 789
        <svg viewBox="0 0 24 24" aria-hidden="true"><path d="M3 9c0-3 4-5 9-5s9 2 9 5v2h-5V9c-1-.6-2.4-1-4-1s-3 .4-4 1v2H3zM6 13h12l2 7H4z"/></svg></li>
      <li>123 456 789
        <svg viewBox="0 0 24 24" aria-hidden="true"><path d="M7 1h10a2 2 0 0 1 2 2v18a2 2 0 0 1-2 2H7a2 2 0 0 1-2-2V3a2 2 0 0 1 2-2zm0 3v14h10V4zm5 15.5a1.2 1.2 0 1 0 0 2.4 1.2 1.2 0 0 0 0-2.4z"/></svg></li>
      <li>info@yourmail.com
        <svg viewBox="0 0 24 24" aria-hidden="true"><path d="M2 5h20v14H2zm2 2v.4l8 5.6 8-5.6V7z"/></svg></li>
      <li>www.yourwebsite.com
        <svg viewBox="0 0 24 24" aria-hidden="true"><circle cx="12" cy="12" r="10"/></svg></li>
    </ul>

    <div class="wordmark">
      <span class="wordmark__name">Ridgeline</span>
      <span class="wordmark__tag">Design + Build</span>
    </div>
  </section>

</main>
</body>
</html>
```